Business cards to launch an education platform

Hi,
I am looking at having new business cards designed.
I am a startup, developing a web platform for schools and university, the education world. It's an online assessment system.
I would like a card that looks classy, and that is using the colors and the font of my logo.

I have attached:
1) my logo
2) A business card that I have designed quickly so you can have all the information required in the card, but I really don't like it.
3) The font that I am using (Lato Regular) to design my web platform
4) Some screenshots of my web platform so you can have a look at the style that I have.

Target Market(s)

Major market: Education system: Schools and university
Minor markets: Business in general

Industry/Entity Type

Business

Contact Information for Business Card

Clara Fenwick
Director

M: 0437 518 902
E: clara.fenwick@amberLoomSystems.com.au

Requirements
Must have
• The colors of my logo

```html
<!DOCTYPE html>
<html lang="en">
<head>
<meta charset="utf-8">
<title>Amber Loom Systems – Business Cards</title>
<link href="https://fonts.googleapis.com/css2?family=Lato:wght@400;700&display=swap" rel="stylesheet">
<style>
  :root {
    --stage: #e9ebee;
    --navy: #1b3a63;
    --navy-ink: #15345c;
    --sky: #2aa3df;
    --sky-soft: #8fc6ee;
    --paper: #ffffff;
    --text-grey: #3d4148;
    --ghost: #eef0f4;
  }
  * { box-sizing: border-box; margin: 0; padding: 0; }
  html, body {
    width: 1200px; height: 675px; overflow: hidden;
    background: var(--stage);
    font-family: "Lato", sans-serif;
  }
  .stage {
    position: relative; width: 1200px; height: 675px;
    display: flex; align-items: center; justify-content: center; gap: 60px;
  }
  .card {
    position: relative; width: 520px; height: 298px;
    box-shadow: 0 6px 18px rgba(20, 30, 50, 0.14);
    overflow: hidden;
  }
  /* Back of card */
  .card--back {
    background: var(--navy);
    display: flex; flex-direction: column; align-items: center; justify-content: center; gap: 18px;
  }
  .brand-square {
    width: 54px; height: 54px; background: var(--sky-soft);
  }
  .brand-name--back {
    color: var(--sky-soft);
    font-size: 30px; font-weight: 400; letter-spacing: 3px;
    text-align: center; line-height: 1.2;
  }
  /* Front of card */
  .card--front { background: var(--paper); }
  .ghost-square {
    position: absolute; right: 28px; top: 70px;
    width: 210px; height: 210px; background: var(--ghost);
  }
  .brand-name--front {
    position: absolute; left: 38px; top: 30px;
    color: var(--navy-ink);
    font-size: 25px; font-weight: 400; letter-spacing: 2.5px; line-height: 1.15;
  }
  .person {
    position: absolute; left: 38px; top: 150px;
  }
  .person-name { color: var(--navy-ink); font-size: 19px; font-weight: 400; }
  .person-role { color: var(--sky); font-size: 12px; margin-top: 1px; }
  .contact-list {
    position: absolute; left: 38px; top: 206px;
    list-style: none; display: flex; flex-direction: column; gap: 5px;
  }
  .contact-item {
    display: flex; align-items: center; gap: 8px;
    color: var(--text-grey); font-size: 13px;
  }
  .contact-icon { width: 12px; height: 12px; flex: none; }
  .contact-icon * { stroke: var(--sky); fill: none; stroke-width: 1.4; }
  .contact-icon .solid { fill: var(--sky); stroke: none; }
</style>
</head>
<body>
<main class="stage">
  <section class="card card--back" aria-label="Card back">
    <div class="brand-square" aria-hidden="true"></div>
    <p class="brand-name--back">Amber Loom<br>Systems</p>
  </section>

  <section class="card card--front" aria-label="Card front">
    <div class="ghost-square" aria-hidden="true"></div>
    <p class="brand-name--front">Amber Loom<br>Systems</p>
    <div class="person">
      <p class="person-name">Clara Fenwick</p>
      <p class="person-role">Director</p>
    </div>
    <ul class="contact-list">
      <li class="contact-item">
        <svg class="contact-icon" viewBox="0 0 12 12" aria-hidden="true"><rect x="3" y="0.8" width="6" height="10.4" rx="1"/><circle class="solid" cx="6" cy="9.3" r="0.7"/></svg>
        0437 518 902
      </li>
      <li class="contact-item">
        <svg class="contact-icon" viewBox="0 0 12 12" aria-hidden="true"><rect class="solid" x="0.5" y="2.5" width="11" height="7" rx="0.5"/><path d="M1 3 L6 7 L11 3" style="stroke:#fff"/></svg>
        clara.fenwick@amberLoomSystems.com.au
      </li>
      <li class="contact-item">
        <svg class="contact-icon" viewBox="0 0 12 12" aria-hidden="true"><circle cx="6" cy="6" r="5"/><ellipse cx="6" cy="6" rx="2.2" ry="5"/><path d="M1 6 H11"/></svg>
        www.amberLoomSystems.com.au
      </li>
    </ul>
  </section>
</main>
</body>
</html>
```